Business Card Design

I need business cards designed for a new company i have started that makes cakes, particularly themed kids cakes with a really modern design and I would like to have my business cards reflect this. I have attached some photos of cakes I have made and would like some to be used.

Industry/Entity Type

Business

Contact Information for Business Card

Business Name: Tarts and Treats by Maren
Mobile: 0492 815 063
email: maren@tartsandtreatsbymaren.example.au
Instagram: instagram.com/tartsandtreatsbymaren/
Facebook: fb.me/tartsandtreatsbymaren

Colors
e667a6
b768aa
3276b5

Requirements
Must have
• Business Name: Tarts and Treats by Maren
• Mobile: 0492 815 063
• email: maren@tartsandtreatsbymaren.example.au
• Instagram: instagram.com/tartsandtreatsbymaren/
• Facebook: fb.me/tartsandtreatsbymaren
Nice to have
• 2 to 3 pictures of my cakes

```html
<!DOCTYPE html>
<html lang="en">
<head>
<meta charset="utf-8">
<title>Tarts and Treats by Maren — Business Card</title>
<link rel="stylesheet" href="https://fonts.googleapis.com/css2?family=Open+Sans:wght@400;600;700&display=swap">
<style>
  :root {
    --pink: #e667a6;
    --pink-deep: #d24f93;
    --pink-pale: #f3c4dc;
    --mauve: #b768aa;
    --blue: #3276b5;
    --ink: #555259;
    --card-white: #ffffff;
    --backdrop: #efebe6;
  }
  * { margin: 0; padding: 0; box-sizing: border-box; }
  html, body {
    width: 1200px;
    height: 843px;
    overflow: hidden;
  }
  body {
    background: var(--backdrop);
    font-family: "Open Sans", Arial, sans-serif;
    position: relative;
  }
  .card {
    position: absolute;
    top: 256px;
    width: 540px;
    height: 330px;
    border-radius: 4px;
    box-shadow: 0 6px 18px rgba(60, 40, 50, 0.18);
    overflow: hidden;
  }

  /* Front */
  .card-front {
    left: 40px;
    background: linear-gradient(135deg, var(--pink) 0%, var(--pink-deep) 100%);
    display: flex;
    align-items: center;
    justify-content: center;
  }
  .brand {
    display: flex;
    align-items: center;
    gap: 16px;
  }
  .brand-dot {
    width: 34px;
    height: 34px;
    border-radius: 50%;
    flex: none;
  }
  .brand-name {
    font-weight: 600;
    line-height: 1.1;
  }
  .card-front .brand-dot { background: var(--card-white); }
  .card-front .brand-name {
    color: var(--card-white);
    font-size: 38px;
  }

  /* Back */
  .card-back {
    left: 620px;
    background: var(--card-white);
  }
  .card-back .brand {
    position: absolute;
    left: 40px;
    top: 38px;
    gap: 12px;
  }
  .card-back .brand-dot {
    width: 26px;
    height: 26px;
    background: var(--pink);
  }
  .card-back .brand-name {
    color: var(--pink);
    font-size: 27px;
  }
  .divider {
    position: absolute;
    left: 40px;
    right: 30px;
    top: 134px;
    height: 2px;
    background: linear-gradient(90deg, var(--pink) 0%, var(--pink-pale) 100%);
  }
  .person {
    position: absolute;
    right: 36px;
    top: 146px;
    text-align: right;
  }
  .person-name {
    color: var(--pink);
    font-size: 19px;
    font-weight: 700;
    letter-spacing: 0.5px;
    text-transform: uppercase;
  }
  .person-role {
    color: var(--ink);
    font-size: 14px;
    margin-top: 2px;
  }
  .contact-list {
    position: absolute;
    left: 36px;
    top: 196px;
    list-style: none;
  }
  .contact-item {
    display: flex;
    align-items: center;
    gap: 10px;
    color: var(--ink);
    font-size: 14px;
    line-height: 20px;
    margin-bottom: 6px;
  }
  .contact-item svg { width: 14px; height: 14px; flex: none; }
  .social-list {
    position: absolute;
    right: 36px;
    top: 264px;
    list-style: none;
  }
  .social-item {
    display: flex;
    align-items: center;
    justify-content: flex-end;
    gap: 10px;
    color: var(--ink);
    font-size: 14px;
    line-height: 20px;
    margin-bottom: 5px;
  }
  .social-mark {
    width: 13px;
    height: 13px;
    border-radius: 2px;
    background: var(--pink);
    flex: none;
  }
</style>
</head>
<body>

  <section class="card card-front" aria-label="Card front">
    <div class="brand">
      <span class="brand-dot"></span>
      <span class="brand-name">Tarts and Treats<br>by Maren</span>
    </div>
  </section>

  <section class="card card-back" aria-label="Card back">
    <div class="brand">
      <span class="brand-dot"></span>
      <span class="brand-name">Tarts and Treats<br>by Maren</span>
    </div>

    <div class="divider"></div>

    <div class="person">
      <p class="person-name">Ada Lindqvist</p>
      <p class="person-role">CEO/Founder</p>
    </div>

    <ul class="contact-list">
      <li class="contact-item">
        <svg viewBox="0 0 14 14" aria-hidden="true">
          <rect x="3.5" y="1" width="7" height="12" rx="1.5" fill="none" stroke="var(--pink)" stroke-width="1.4"/>
          <line x1="6" y1="11" x2="8" y2="11" stroke="var(--pink)" stroke-width="1.2"/>
        </svg>
        <span>0492 815 063</span>
      </li>
      <li class="contact-item">
        <svg viewBox="0 0 14 14" aria-hidden="true">
          <rect x="1" y="3" width="12" height="8.5" rx="1" fill="var(--pink)"/>
          <polyline points="1.5,3.6 7,8 12.5,3.6" fill="none" stroke="#fff" stroke-width="1.1"/>
        </svg>
        <span>maren@tartsandtreatsbymaren.example.au</span>
      </li>
    </ul>

    <ul class="social-list">
      <li class="social-item">
        <span>tartsandtreatsbymaren</span>
        <span class="social-mark"></span>
      </li>
      <li class="social-item">
        <span>tartsandtreatsbymaren</span>
        <span class="social-mark"></span>
      </li>
    </ul>
  </section>

</body>
</html>
```